Vape Brand Cartoon Packaging Design

I AM NOT PICKY!! Just need to get the basic job done and I will be happy. To start we need a text logo for our brand "Poma Frost" vape cartridges that is colorful, with a cartoonish design. We have 3 flavors we are starting with that need there own custom logo: Lagoon Drizzle (colorful pink packaging with ice cream sherbert incorporated in the cartoon design), Harbor Fudge (blue background with a white cake cartoon design), and Rocket Waffles (orange packaging with cartoon animated zimbo cookies acting crazy/fighting on it). I dont care if the images are sourced from google images or wherever. See the uploaded files for guidance I want them extremely similar to that packaging. The packaging is roughly 1.5 inches wide and 2.5 inches tall.
Where the packaging says "high ridge rarities" I want my brand name "Poma Frost", underneath it I want it to say "vape cartridge" just like in the picture. I also want the flavors in the same area on the package and for them all to say HYBRID and 1.0 gram in the same spot. Instead of 1.0 gram though have it say 1000 mg. To reiterate I want the packaging very similar to the packaging in the picture. There will be other flavors added in the near future so ideally I want someone I can work with in the long term!
Poma Frost

```html
<!DOCTYPE html>
<html lang="en">
<head>
<meta charset="utf-8">
<title>Poma Frost – Lagoon Drizzle Vape Cartridge</title>
<link rel="stylesheet" href="https://fonts.googleapis.com/css2?family=Bangers&display=swap">
<style>
  :root {
    --pink: #e8407c;
    --pink-light: #f25c95;
    --pink-text: #f3a3c6;
    --star-pink: #ec4f8a;
    --ink: #2c0b26;
    --plum-dark: #3f1442;
    --plum-mid: #7b3f9c;
    --plum-shape: #8a2a6e;
    --ring-light: #9fd4ef;
    --ring-deep: #0e8fd0;
    --ring-teal: #10b6d4;
    --disc: #f2f2f2;
    --cone-top: #ea3f7c;
    --cone-base: #e0a862;
  }
  html, body {
    margin: 0;
    padding: 0;
    width: 1200px;
    height: 2400px;
    overflow: hidden;
    background: var(--pink);
  }
  .package {
    display: block;
    width: 1200px;
    height: 2400px;
  }
  .label-text {
    font-family: "Bangers", "Comic Sans MS", cursive;
    fill: var(--pink-text);
    stroke: var(--ink);
    paint-order: stroke fill;
    stroke-linejoin: round;
    text-anchor: middle;
  }
  .flavor-name { font-size: 118px; stroke-width: 9px; letter-spacing: 2px; }
  .brand-name { font-size: 205px; stroke-width: 11px; letter-spacing: 2px; }
  .product-type { font-size: 132px; stroke-width: 9px; letter-spacing: 1px; }
  .strain-type { font-size: 172px; stroke-width: 10px; letter-spacing: 3px; }
  .strength { font-size: 134px; stroke-width: 9px; letter-spacing: 2px; }
  .star-pink { fill: var(--star-pink); }
  .star-plum { fill: url(#plum-star); }
  .accent-shape { fill: var(--plum-shape); }
</style>
</head>
<body>
<svg class="package" viewBox="0 0 1200 2400" xmlns="http://www.w3.org/2000/svg">
  <defs>
    <radialGradient id="pink-field" cx="0.45" cy="0.5" r="0.7">
      <stop offset="0" stop-color="var(--pink-light)"/>
      <stop offset="1" stop-color="var(--pink)"/>
    </radialGradient>
    <radialGradient id="plum-band-top" cx="0.5" cy="0.15" r="0.6">
      <stop offset="0" stop-color="var(--plum-mid)"/>
      <stop offset="1" stop-color="var(--plum-dark)"/>
    </radialGradient>
    <radialGradient id="plum-band-bottom" cx="0.5" cy="0.5" r="0.6">
      <stop offset="0" stop-color="var(--plum-mid)"/>
      <stop offset="1" stop-color="var(--plum-dark)"/>
    </radialGradient>
    <radialGradient id="plum-star" cx="0.5" cy="0.5" r="0.5">
      <stop offset="0" stop-color="var(--plum-mid)"/>
      <stop offset="1" stop-color="var(--plum-dark)"/>
    </radialGradient>
    <linearGradient id="badge-ring" x1="0" y1="0" x2="1" y2="1">
      <stop offset="0" stop-color="var(--ring-light)"/>
      <stop offset="0.55" stop-color="var(--ring-deep)"/>
      <stop offset="1" stop-color="var(--ring-teal)"/>
    </linearGradient>
    <linearGradient id="cone-art" x1="0" y1="0" x2="0" y2="1">
      <stop offset="0" stop-color="var(--cone-top)"/>
      <stop offset="0.48" stop-color="var(--cone-top)"/>
      <stop offset="0.6" stop-color="var(--cone-base)"/>
      <stop offset="1" stop-color="var(--cone-base)"/>
    </linearGradient>
    <path id="star" d="M0,-1 L0.265,-0.364 0.951,-0.309 0.428,0.139 0.588,0.809 0,0.45 -0.588,0.809 -0.428,0.139 -0.951,-0.309 -0.265,-0.364Z"/>
    <path id="brand-arc" d="M130,610 Q600,190 1080,610"/>
  </defs>

  <!-- background -->
  <rect class="field" width="1200" height="2400" fill="url(#pink-field)"/>

  <!-- top drip band -->
  <path class="band band-top" fill="url(#plum-band-top)"
        d="M0,0 H1200 V320 C1150,300 1090,250 1010,268 C940,284 900,250 820,232
           C740,216 660,250 560,232 C470,216 420,262 330,272 C250,280 200,240 140,300
           C100,340 40,350 0,330 Z"/>

  <!-- bottom drip band -->
  <path class="band band-bottom" fill="url(#plum-band-bottom)"
        d="M0,2400 H1200 V2076 C1150,2060 1080,2066 1020,2090 C960,2112 900,2080 860,2090
           C800,2106 760,2130 700,2120 C620,2106 580,2060 500,2060 C420,2060 380,2110 300,2100
           C230,2092 190,2050 120,2056 C70,2060 30,2084 0,2090 Z"/>

  <!-- band stars -->
  <use class="star-pink" href="#star" transform="translate(99,160) rotate(-12) scale(56)"/>
  <use class="star-pink" href="#star" transform="translate(1100,189) rotate(10) scale(32)"/>
  <use class="star-pink" href="#star" transform="translate(160,2264) rotate(-8) scale(48)"/>
  <use class="star-pink" href="#star" transform="translate(1104,2320) rotate(12) scale(51)"/>

  <!-- flavor / brand / product -->
  <text class="label-text flavor-name" x="600" y="160">LAGOON DRIZZLE</text>
  <text class="label-text brand-name"><textPath href="#brand-arc" startOffset="50%">POMA FROST</textPath></text>
  <text class="label-text product-type" x="600" y="784">VAPE CARTRIDGE</text>

  <!-- accent shapes behind badge -->
  <polygon class="accent-shape" points="1010,1080 1132,1104 1050,1176"/>
  <polygon class="accent-shape" points="176,1748 300,1648 360,1768"/>

  <!-- badge -->
  <g class="badge">
    <circle class="badge-ring" cx="616" cy="1352" r="480" fill="url(#badge-ring)"/>
    <circle class="badge-disc" cx="616" cy="1352" r="424" fill="var(--disc)"/>
    <rect class="badge-art" role="img" aria-label="Cartoon pink sherbet ice cream cone"
          x="408" y="872" width="424" height="840" rx="90" fill="url(#cone-art)"/>
  </g>

  <!-- badge stars -->
  <use class="star-pink" href="#star" transform="translate(371,1064) rotate(-6) scale(60)"/>
  <use class="star-pink" href="#star" transform="translate(1000,1523) rotate(14) scale(32)"/>
  <use class="star-pink" href="#star" transform="translate(408,1648) rotate(-10) scale(60)"/>
  <use class="star-plum" href="#star" transform="translate(1000,1000) rotate(10) scale(82)"/>
  <use class="star-plum" href="#star" transform="translate(800,1792) rotate(-6) scale(122)"/>
  <use class="star-plum" href="#star" transform="translate(168,1864) rotate(-14) scale(45)"/>

  <!-- strain + strength -->
  <text class="label-text strain-type" x="620" y="2200">HYBRID</text>
  <text class="label-text strength" x="612" y="2346">1000 MG</text>
</svg>
</body>
</html>
```